Software Development Consulting Company Needs Business Card Design

We need a new business card design for our consultants at Kestrel Works (kestrelworks.example). We are a small firm that provides high-end software development and methodology consulting to medium to large enterprise IT organizations.

Our logo uses Futura for the font and we would like to stick with navy blue and canary yellow for the logo colors. Attached are normal and reversed versions of our logos in illustrator format.
Updates

Hi Everyone, Thank yo very much for your amazing design ideas. I have created a poll for this project and our employees will be voting on the design they wish to use. We will be making a decision this Wednesday (October 22nd). Thanks again, Dale Hartwick

Industry/Entity Type

Business

```html
<!DOCTYPE html>
<html lang="en">
<head>
<meta charset="utf-8">
<title>Kestrel Works — Business Card</title>
<link rel="stylesheet" href="https://fonts.googleapis.com/css2?family=Jost:wght@400;500&family=Open+Sans:wght@400;600&display=swap">
<style>
  :root {
    --navy: #1c4a6e;
    --canary: #f2e21a;
    --white: #ffffff;
    --ink: #1c4a6e;
    --stage: #eceae6;
  }
  * { margin: 0; padding: 0; box-sizing: border-box; }
  html, body { width: 1200px; height: 720px; overflow: hidden; }
  body {
    background: var(--stage);
    font-family: "Open Sans", Arial, sans-serif;
    position: relative;
  }
  .card {
    position: absolute;
    width: 540px;
    height: 309px;
    top: 205px;
    overflow: hidden;
    box-shadow: 0 2px 6px rgba(0,0,0,0.18);
  }
  .card--front { left: 40px; background: var(--white); }
  .card--back { left: 620px; background: var(--navy); }

  .front-shape { position: absolute; inset: 0; width: 540px; height: 309px; }

  .wordmark {
    position: absolute;
    display: flex;
    align-items: center;
    gap: 12px;
    font-family: "Jost", "Futura", sans-serif;
    font-weight: 500;
    letter-spacing: 0.14em;
    white-space: nowrap;
  }
  .wordmark__dot {
    width: 22px; height: 22px;
    border-radius: 50%;
    background: var(--canary);
    flex: none;
  }
  .card--front .wordmark { left: 132px; top: 72px; font-size: 34px; color: var(--ink); }
  .card--back .wordmark { left: 50%; top: 108px; transform: translateX(-50%); font-size: 38px; color: var(--white); }

  .person {
    position: absolute;
    right: 262px;
    top: 200px;
    text-align: right;
    color: var(--white);
    line-height: 1.3;
  }
  .person__name { font-size: 17px; font-weight: 600; }
  .person__title { font-size: 12px; }
  .person__place { font-size: 12px; }

  .divider {
    position: absolute;
    left: 290px; top: 190px;
    width: 1px; height: 78px;
    background: rgba(255,255,255,0.8);
  }
  .contact {
    position: absolute;
    left: 304px; top: 172px;
    list-style: none;
    color: var(--white);
    font-size: 12px;
    line-height: 21px;
  }
  .contact li { display: flex; align-items: center; gap: 7px; }
  .contact svg { width: 12px; height: 12px; flex: none; }

  .back-domain {
    position: absolute;
    left: 0; right: 0;
    text-align: center;
    color: var(--white);
    font-size: 15px;
    letter-spacing: 0.14em;
  }
  .back-domain--upper { top: 168px; }
  .back-domain--lower { top: 250px; }
</style>
</head>
<body>
  <section class="card card--front" aria-label="Card front">
    <svg class="front-shape" viewBox="0 0 540 309" aria-hidden="true">
      <path d="M0 300 Q 250 132 540 122" fill="none" stroke="var(--canary)" stroke-width="5"/>
      <path d="M0 309 Q 250 142 540 132 L540 309 Z" fill="var(--navy)"/>
    </svg>

    <div class="wordmark"><span class="wordmark__dot"></span>KESTREL WORKS</div>

    <div class="person">
      <div class="person__name">Your Name</div>
      <div class="person__title">Title</div>
      <div class="person__place">Lakeport + Millbrook, IL</div>
    </div>

    <div class="divider"></div>

    <ul class="contact">
      <li>
        <svg viewBox="0 0 12 12" aria-hidden="true"><circle cx="6" cy="6" r="5.5" fill="none" stroke="#fff"/><path d="M4 3 L5 5 L4.5 5.6 Q5.5 7 6.6 7.5 L7.2 7 L9 8 L8.4 9 Q5 9 3 4 Z" fill="#fff"/></svg>
        012-555-0147
      </li>
      <li>
        <svg viewBox="0 0 12 12" aria-hidden="true"><rect x="1" y="3" width="10" height="7" fill="#fff"/><path d="M1 3 L6 7 L11 3" fill="none" stroke="var(--navy)"/></svg>
        info@kestrelworks.example
      </li>
      <li>
        <svg viewBox="0 0 12 12" aria-hidden="true"><circle cx="6" cy="6" r="5" fill="none" stroke="#fff"/><ellipse cx="6" cy="6" rx="2.2" ry="5" fill="none" stroke="#fff"/><path d="M1 6 H11" stroke="#fff"/></svg>
        www.kestrelworks.example
      </li>
    </ul>
  </section>

  <section class="card card--back" aria-label="Card back">
    <div class="wordmark"><span class="wordmark__dot"></span>KESTREL WORKS</div>
    <p class="back-domain back-domain--upper">kestrelworks.example</p>
    <p class="back-domain back-domain--lower">www.kestrelworks.example</p>
  </section>
</body>
</html>
```